Business Card for Coach - ready to print

Design Business Card ready to order prints www.lukasbrenner.coach

* An Overview / Background of the Business & Services
· Coaching
· Personal growth
* The Target Market / Audience you are trying to reach
· private person in different roles (self, familiy, business role)s
* Design Specifics; any preferences or ideas for Style, Colour, Imagery, etc
· See www.lukasbrenner.coach
· "simple" design
· (small) element of surprise / unusual element

* Information that will be placed in the Business Card
· Beratung und Coaching
· Address: Lukas Brenner, Mosering 42, CH-8312 Winterthur, Mobile +41 79 264 53 07
* Do you have an existing website or Facebook page where designers can learn more about your company?
· lukasbrenner.coach

Target Market(s)

private person in different roles (self, familiy, business role)

Industry/Entity Type

Life Coaching

Contact Information for Business Card

Lukas Brenner
Mosering 42
CH-8312 Winterthur

Mobile: +41 79 264 53 07
Email: lubr@alpimail.ch
www.lukasbrenner.coach

Font styles to use
Sans Serif

Colors

Designer to choose colors to be used in the design.

Requirements
Must have
• "simple" design
• element of surprise / unusual element
• Beratung & Coaching
• see www.lukasbrenner.coach for colors and so...
Nice to have
• TA Symbol (three rings on top of each other) - unsual presentation
• QR Code of Website (see if it fits in and still looks good).

```html
<!DOCTYPE html>
<html lang="de">
<head>
<meta charset="utf-8">
<title>Lukas Brenner – Visitenkarte</title>
<link rel="stylesheet" href="https://fonts.googleapis.com/css2?family=Montserrat:wght@400;500;700&display=swap">
<style>
  :root{
    --red:#b01a2b;
    --red-deep:#a0172a;
    --orange:#ee8a17;
    --ink:#2b2b2b;
    --paper:#f6f6f6;
    --stage:#d9d9d9;
  }
  *{margin:0;padding:0;box-sizing:border-box}
  html,body{width:1200px;height:1021px;overflow:hidden}
  body{background:var(--stage);font-family:"Montserrat",sans-serif;position:relative}
  .card{position:absolute;left:260px;width:680px;height:389px;box-shadow:0 10px 28px rgba(0,0,0,.25)}
  .card--front{top:66px;background:linear-gradient(160deg,#bf1d2f,var(--red-deep));display:flex;flex-direction:column;align-items:center;justify-content:center;color:#fff}
  .card--back{top:566px;background:var(--paper)}
  .brand{display:flex;align-items:center;gap:12px}
  .brand__dot{width:14px;height:14px;border-radius:50%;background:var(--orange)}
  .brand__name{font-weight:700;font-size:38px;letter-spacing:1.5px;text-transform:uppercase}
  .tagline{font-size:21px;font-weight:400;margin-top:4px;letter-spacing:.5px}
  .card--front .brand__name{color:#fff}
  .card--back .brand{position:absolute;left:46px;top:138px}
  .card--back .brand__name{color:var(--red);font-size:30px}
  .card--back .tagline{position:absolute;left:72px;top:182px;color:var(--ink);font-size:17px}
  .contact{position:absolute;left:390px;top:116px;color:var(--ink);font-size:17px;line-height:1.3}
  .contact__address{margin-bottom:16px}
  .contact__row{display:flex;align-items:center;gap:8px}
  .contact__row svg{width:14px;height:14px;flex:none}
  .stripe{position:absolute;bottom:0;left:0;width:100%;height:20px;display:flex;gap:4px}
  .stripe__seg--red{background:var(--red)}
  .stripe__seg--orange{background:var(--orange)}
</style>
</head>
<body>
  <section class="card card--front">
    <div class="brand"><span class="brand__dot"></span><span class="brand__name">Lukas Brenner</span></div>
    <p class="tagline">Beratung &amp; Coaching</p>
  </section>

  <section class="card card--back">
    <div class="brand"><span class="brand__dot"></span><span class="brand__name">Lukas Brenner</span></div>
    <p class="tagline">Beratung &amp; Coaching</p>

    <div class="contact">
      <p class="contact__address">Mosering 42<br>CH-8312 Winterthur</p>
      <p class="contact__row">
        <svg viewBox="0 0 14 14"><rect x="3.5" y="1" width="7" height="12" rx="1.3" fill="none" stroke="#ee8a17" stroke-width="1.3"/><circle cx="7" cy="10.8" r=".8" fill="#ee8a17"/></svg>
        +41 79 264 53 07</p>
      <p class="contact__row">
        <svg viewBox="0 0 14 14"><rect x="1" y="3" width="12" height="8.5" fill="none" stroke="#ee8a17" stroke-width="1.3"/><path d="M1 3l6 5 6-5" fill="none" stroke="#ee8a17" stroke-width="1.3"/></svg>
        lubr@alpimail.ch</p>
      <p class="contact__row">
        <svg viewBox="0 0 14 14"><circle cx="7" cy="7" r="5.8" fill="none" stroke="#ee8a17" stroke-width="1.2"/><ellipse cx="7" cy="7" rx="2.6" ry="5.8" fill="none" stroke="#ee8a17" stroke-width="1"/><path d="M1.2 7h11.6" stroke="#ee8a17" stroke-width="1"/></svg>
        www.lukasbrenner.coach</p>
    </div>

    <div class="stripe">
      <span class="stripe__seg--red" style="flex:0 0 44%"></span>
      <span class="stripe__seg--orange" style="flex:1"></span>
      <span class="stripe__seg--red" style="flex:0 0 7%"></span>
    </div>
  </section>
</body>
</html>
```